Bicycle Sales Company

I need a bicycle sales site for pre-orders, 3-4 models, multiple colors per order. The bikes are electric bikes, company logo color scheme has red. Maybe a countdown to a date when pre-order will close. I also want to incorporate a deposit style system for the pre-order with the balance due on shipping.

```html
<!DOCTYPE html>
<html lang="en">
<head>
<meta charset="utf-8">
<title>Bicycle Sales – Electric Bike Pre-Order</title>
<link href="https://fonts.googleapis.com/css2?family=Poppins:ital,wght@0,300;0,400;0,500;0,600;0,700;0,800;1,600&display=swap" rel="stylesheet">
<style>
:root{
  --red:#b5161f;
  --red-dark:#8f1119;
  --ink:#1c1c1c;
  --text:#3a3a3a;
  --muted:#777;
  --card:#f1f1f1;
  --white:#fff;
  --footer:#1d1d1d;
  --tan:#a08c72;
  --blue:#1f4fd1;
}
*{box-sizing:border-box;margin:0;padding:0}
html,body{width:1200px;height:4501px;overflow:hidden;background:var(--white)}
body{font-family:'Poppins',sans-serif;color:var(--text)}
.page{position:relative;width:1200px;height:4501px;overflow:hidden}
.abs{position:absolute}

.hero{left:0;top:0;width:1200px;height:514px;background:linear-gradient(100deg,#b3202a 0%,#c02530 55%,#b41f29 100%)}
.hero-bg{left:560px;top:120px;width:560px;height:380px;background:radial-gradient(ellipse at 40% 60%,rgba(120,10,20,.35),rgba(0,0,0,0) 70%)}
.logo{font-weight:700;font-size:26px;letter-spacing:1px;color:var(--white);text-transform:uppercase}
.nav{left:528px;top:36px;display:flex;gap:22px;font-size:15px;color:var(--white)}
.nav-sep{left:965px;top:36px;width:1px;height:20px;background:rgba(255,255,255,.5)}
.cart{left:1045px;top:28px;width:44px;height:44px;border-radius:50%;background:var(--white)}
.hero-bike{left:110px;top:120px;width:425px;height:360px;border-radius:30px;background:linear-gradient(135deg,#2a3f9e,#1b1b22 70%);opacity:.85}
.welcome{left:620px;top:148px;width:465px;text-align:center;color:var(--white);font-size:24px;font-weight:500}
.hero-title{left:600px;top:172px;width:505px;text-align:center;color:var(--white);font-size:64px;font-weight:600;line-height:1.05}
.close-line{left:620px;top:276px;width:465px;text-align:center;color:var(--white);font-size:20px;font-weight:600;font-style:italic}
.count{left:706px;top:325px;display:flex;gap:18px}
.unit{width:60px;text-align:center}
.unit .num{height:68px;background:#1e1416;border-radius:4px;color:var(--white);font-size:30px;font-weight:600;line-height:68px}
.unit .lbl{margin-top:8px;font-size:12px;font-weight:600;color:var(--white);letter-spacing:.3px}

.section-title{width:1200px;left:0;text-align:center;font-size:40px;font-weight:400;color:var(--ink);letter-spacing:.5px}
.section-title b{font-weight:700}

.card{width:480px;height:323px;background:var(--card)}
.card-img{width:360px;height:240px;border-radius:20px}
.card-name{font-size:20px;font-weight:600;color:var(--ink)}
.card-price{font-size:21px;color:var(--text)}
.swatches{display:flex;gap:9px;align-items:center}
.sw{width:16px;height:16px;border-radius:50%}
.sw.sel{box-shadow:0 0 0 2px #fff,0 0 0 3px #888}
.feat{font-size:15px;display:flex;align-items:center;gap:12px;color:var(--text)}
.btn{display:inline-block;height:44px;line-height:42px;padding:0 22px;font-size:14px;font-weight:600;text-transform:uppercase;letter-spacing:.3px}
.btn-red{background:var(--red);color:var(--white);border:1px solid var(--red)}
.btn-line{border:2px solid #b9b9b9;color:#888;background:transparent}

.about{left:0;top:1953px;width:1200px;height:555px;background:linear-gradient(90deg,#201012 0%,#2c1315 40%,#6a4030 60%,#d07a3c 80%,#e8a05a 100%)}
.about-photo{width:640px;height:555px;background:linear-gradient(180deg,rgba(230,150,80,0),rgba(40,25,25,.55))}
.about h2{font-size:40px;font-weight:400;color:var(--white)}
.about-text{font-size:15.5px;line-height:28px;color:var(--white)}

.review-photo{left:112px;top:2680px;width:388px;height:388px;border-radius:50%;background:linear-gradient(160deg,#c7ccd3,#6f7a82 55%,#3a3a3a);box-shadow:8px 8px 0 var(--red)}
.arrow{width:34px;height:34px;border-radius:50%}
.review-text{left:580px;top:2790px;width:440px;font-size:15.5px;line-height:28px;color:var(--text)}

.gallery{left:112px;top:3232px;display:grid;grid-template-columns:repeat(4,240px);grid-auto-rows:240px;gap:6px}
.tile{width:240px;height:240px}

.reserve{left:0;top:3863px;width:1200px;height:305px;background:linear-gradient(90deg,#f7eef0 0%,#f1dde1 55%,#e3b6bd 100%)}
.reserve h3{font-size:25px;font-weight:600;line-height:41px;color:var(--ink)}
.reserve h3 span{color:var(--red)}

.footer{left:0;top:4168px;width:1200px;height:333px;background:var(--footer);color:#e4e4e4}
.f-head{font-size:14px;font-weight:500;color:var(--white);text-transform:uppercase}
.f-bar{width:40px;height:2px;background:var(--white);margin-top:12px}
.f-list{list-style:none;font-size:14px;line-height:30px;color:#dcdcdc;margin-top:20px}
.social{width:30px;height:30px;border:1.5px solid #ddd;border-radius:50%}
</style>
</head>
<body>
<div class="page">

  <header class="abs hero">
    <div class="abs hero-bg"></div>
    <div class="abs logo" style="left:112px;top:30px">Bicycle Sales</div>
    <nav class="abs nav"><span>Home</span><span>About</span><span>Products</span><span>Review</span><span>Blog</span><span>Contact</span></nav>
    <div class="abs nav-sep"></div>
    <svg class="abs" style="left:990px;top:36px" width="22" height="22" viewBox="0 0 22 22" fill="none" stroke="#fff" stroke-width="2"><circle cx="9" cy="9" r="7"/><path d="M14 14l6 6"/></svg>
    <div class="abs cart"></div>
    <svg class="abs" style="left:1056px;top:38px" width="22" height="24" viewBox="0 0 22 24" fill="none" stroke="#b5161f" stroke-width="2"><path d="M3 7h16l-1 15H4z"/><path d="M7 9V5a4 4 0 018 0v4"/></svg>
    <div class="abs hero-bike" role="img" aria-label="Blue electric mountain bike, side view"></div>
    <div class="abs welcome">WELCOME</div>
    <h1 class="abs hero-title">BICYCLE SALES</h1>
    <div class="abs close-line">PRE-ORDER WILL CLOSE IN</div>
    <div class="abs count">
      <div class="unit"><div class="num">01</div><div class="lbl">DAYS</div></div>
      <div class="unit"><div class="num">01</div><div class="lbl">HOURS</div></div>
      <div class="unit"><div class="num">01</div><div class="lbl">MINUTES</div></div>
      <div class="unit"><div class="num">01</div><div class="lbl">SECONDS</div></div>
    </div>
  </header>

  <h2 class="abs section-title" style="top:570px">OUR <b>BICYCLES</b></h2>

  <div class="abs card" style="left:112px;top:892px"></div>
  <div class="abs card-img" role="img" aria-label="Bicycle 1: tan electric city bike with rear rack" style="left:170px;top:680px;background:linear-gradient(135deg,#cdbfa8,#5a4e40)"></div>
  <div class="abs card-name" style="left:164px;top:968px">BYCYCLE 1</div>
  <div class="abs swatches" style="left:438px;top:974px"><span class="sw sel" style="background:var(--tan)"></span><span class="sw" style="background:#1d1d1d"></span><span class="sw" style="background:var(--blue)"></span><span class="sw" style="background:var(--red)"></span></div>
  <div class="abs card-price" style="left:164px;top:1006px">$148</div>
  <div class="abs feat" style="left:164px;top:1053px"><svg width="14" height="14" viewBox="0 0 14 14"><circle cx="7" cy="7" r="6" fill="none" stroke="#b5161f" stroke-width="1.6"/><path d="M4 7l2 2 4-4" fill="none" stroke="#b5161f" stroke-width="1.6"/></svg>Upto 30kms in one charge</div>
  <div class="abs feat" style="left:164px;top:1087px"><svg width="14" height="14" viewBox="0 0 14 14"><circle cx="7" cy="7" r="6" fill="none" stroke="#b5161f" stroke-width="1.6"/><path d="M4 7l2 2 4-4" fill="none" stroke="#b5161f" stroke-width="1.6"/></svg>Detachable Batteries</div>
  <span class="abs btn btn-red" style="left:164px;top:1135px">Pre-Order</span>
  <span class="abs btn btn-line" style="left:310px;top:1135px">Buy Now</span>

  <div class="abs card" style="left:610px;top:892px"></div>
  <div class="abs card-img" role="img" aria-label="Bicycle 2: black electric mountain bike with red rims" style="left:670px;top:680px;background:linear-gradient(135deg,#9a9a9a,#1e1e1e)"></div>
  <div class="abs card-name" style="left:663px;top:968px">BYCYCLE 2</div>
  <div class="abs swatches" style="left:936px;top:974px"><span class="sw" style="background:var(--tan)"></span><span class="sw sel" style="background:#1d1d1d"></span><span class="sw" style="background:var(--blue)"></span><span class="sw" style="background:var(--red)"></span></div>
  <div class="abs card-price" style="left:663px;top:1006px">$148</div>
  <div class="abs feat" style="left:663px;top:1053px"><svg width="14" height="14" viewBox="0 0 14 14"><circle cx="7" cy="7" r="6" fill="none" stroke="#b5161f" stroke-width="1.6"/><path d="M4 7l2 2 4-4" fill="none" stroke="#b5161f" stroke-width="1.6"/></svg>Upto 30kms in one charge</div>
  <div class="abs feat" style="left:663px;top:1087px"><svg width="14" height="14" viewBox="0 0 14 14"><circle cx="7" cy="7" r="6" fill="none" stroke="#b5161f" stroke-width="1.6"/><path d="M4 7l2 2 4-4" fill="none" stroke="#b5161f" stroke-width="1.6"/></svg>Detachable Batteries</div>
  <span class="abs btn btn-red" style="left:663px;top:1135px">Pre-Order</span>
  <span class="abs btn btn-line" style="left:810px;top:1135px">Buy Now</span>

  <div class="abs card" style="left:112px;top:1525px"></div>
  <div class="abs card-img" role="img" aria-label="Bicycle 3: dark grey electric mountain bike" style="left:165px;top:1312px;background:linear-gradient(135deg,#a8a8a8,#2a2a2a)"></div>
  <div class="abs card-name" style="left:164px;top:1602px">BYCYCLE 3</div>
  <div class="abs swatches" style="left:438px;top:1608px"><span class="sw" style="background:var(--tan)"></span><span class="sw sel" style="background:#1d1d1d"></span><span class="sw" style="background:var(--blue)"></span><span class="sw" style="background:var(--red)"></span></div>
  <div class="abs card-price" style="left:164px;top:1640px">$148</div>
  <div class="abs feat" style="left:164px;top:1687px"><svg width="14" height="14" viewBox="0 0 14 14"><circle cx="7" cy="7" r="6" fill="none" stroke="#b5161f" stroke-width="1.6"/><path d="M4 7l2 2 4-4" fill="none" stroke="#b5161f" stroke-width="1.6"/></svg>Upto 30kms in one charge</div>
  <div class="abs feat" style="left:164px;top:1721px"><svg width="14" height="14" viewBox="0 0 14 14"><circle cx="7" cy="7" r="6" fill="none" stroke="#b5161f" stroke-width="1.6"/><path d="M4 7l2 2 4-4" fill="none" stroke="#b5161f" stroke-width="1.6"/></svg>Detachable Batteries</div>
  <span class="abs btn btn-red" style="left:164px;top:1769px">Pre-Order</span>
  <span class="abs btn btn-line" style="left:310px;top:1769px">Buy Now</span>

  <div class="abs card" style="left:610px;top:1525px"></div>
  <div class="abs card-img" role="img" aria-label="Bicycle 4: blue electric mountain bike" style="left:680px;top:1312px;background:linear-gradient(135deg,#8ea5e6,#24306a 65%,#1e1e1e)"></div>
  <div class="abs card-name" style="left:663px;top:1602px">BYCYCLE 4</div>
  <div class="abs swatches" style="left:936px;top:1608px"><span class="sw" style="background:var(--tan)"></span><span class="sw" style="background:#1d1d1d"></span><span class="sw sel" style="background:var(--blue)"></span><span class="sw" style="background:var(--red)"></span></div>
  <div class="abs card-price" style="left:663px;top:1640px">$148</div>
  <div class="abs feat" style="left:663px;top:1687px"><svg width="14" height="14" viewBox="0 0 14 14"><circle cx="7" cy="7" r="6" fill="none" stroke="#b5161f" stroke-width="1.6"/><path d="M4 7l2 2 4-4" fill="none" stroke="#b5161f" stroke-width="1.6"/></svg>Upto 30kms in one charge</div>
  <div class="abs feat" style="left:663px;top:1721px"><svg width="14" height="14" viewBox="0 0 14 14"><circle cx="7" cy="7" r="6" fill="none" stroke="#b5161f" stroke-width="1.6"/><path d="M4 7l2 2 4-4" fill="none" stroke="#b5161f" stroke-width="1.6"/></svg>Detachable Batteries</div>
  <span class="abs btn btn-red" style="left:663px;top:1769px">Pre-Order</span>
  <span class="abs btn btn-line" style="left:808px;top:1769px">Buy Now</span>

  <section class="abs about">
    <div class="abs about-photo" role="img" aria-label="Electric bike parked on a waterfront promenade at sunset" style="left:560px;top:0"></div>
    <h2 class="abs" style="left:112px;top:75px">ABOUT <b>US</b></h2>
    <p class="abs about-text" style="left:112px;top:164px;width:490px">Lorem ipsum dolor sit amet, consectetur adipiscing elit, sed do eiusmod tempor incididunt ut labore et dolore magna aliqua. Quis ipsum suspendisse ultric sus commodo viverra maecenas accumsan lacus vel facilisis.</p>
    <p class="abs about-text" style="left:112px;top:292px;width:495px">Consectetur adipiscing elit, sed do eiusmod tempor incididunt ut labore et dolore magna aliqua. Quis ipsum suspendisse ultric sus commodo viverra maecenas accumsan lacus vel facilisis.</p>
    <span class="abs btn btn-red" style="left:112px;top:418px">Learn More</span>
  </section>

  <h2 class="abs section-title" style="top:2578px">CLIENT <b>REVIEWS</b></h2>
  <svg class="abs arrow" style="left:36px;top:2856px" viewBox="0 0 34 34"><circle cx="17" cy="17" r="16" fill="#d8d8d8"/><path d="M20 10l-7 7 7 7" fill="none" stroke="#fff" stroke-width="2.5"/></svg>
  <svg class="abs arrow" style="left:1121px;top:2856px" viewBox="0 0 34 34"><circle cx="17" cy="17" r="16" fill="#6a6a6a"/><path d="M14 10l7 7-7 7" fill="none" stroke="#fff" stroke-width="2.5"/></svg>
  <div class="abs review-photo" role="img" aria-label="Commuter riding an electric bike through a city street"></div>
  <svg class="abs" style="left:978px;top:2700px" width="70" height="70" viewBox="0 0 70 70"><circle cx="35" cy="35" r="34" fill="#f1c5c9"/><circle cx="35" cy="35" r="28" fill="#b5161f"/><path d="M24 42c4-2 6-5 6-9h-5v-7h8v7c0 6-3 10-8 12zM37 42c4-2 6-5 6-9h-5v-7h8v7c0 6-3 10-8 12z" fill="#fff"/></svg>
  <svg class="abs" style="left:580px;top:2767px" width="50" height="10" viewBox="0 0 50 10"><g fill="#e6a817"><polygon points="5,0 6.2,3.6 10,3.6 7,5.8 8.1,9.5 5,7.2 1.9,9.5 3,5.8 0,3.6 3.8,3.6"/><polygon transform="translate(10 0)" points="5,0 6.2,3.6 10,3.6 7,5.8 8.1,9.5 5,7.2 1.9,9.5 3,5.8 0,3.6 3.8,3.6"/><polygon transform="translate(20 0)" points="5,0 6.2,3.6 10,3.6 7,5.8 8.1,9.5 5,7.2 1.9,9.5 3,5.8 0,3.6 3.8,3.6"/><polygon transform="translate(30 0)" points="5,0 6.2,3.6 10,3.6 7,5.8 8.1,9.5 5,7.2 1.9,9.5 3,5.8 0,3.6 3.8,3.6"/><polygon transform="translate(40 0)" points="5,0 6.2,3.6 10,3.6 7,5.8 8.1,9.5 5,7.2 1.9,9.5 3,5.8 0,3.6 3.8,3.6"/></g></svg>
  <p class="abs review-text">Lorem ipsum dolor sit amet, consectetur adipiscing elit, sed do eiusmod tempor incididunt ut labore et dolore magna aliqua. Quis ipsum suspendisse ultrices gravida. Risus commodo viverra maecenas accumsan lacus vel.</p>
  <div class="abs" style="left:580px;top:2930px;width:52px;height:52px;border-radius:50%;background:#1c1c1c;box-shadow:0 0 0 3px #f1c5c9"></div>
  <div class="abs" style="left:658px;top:2930px;font-size:15px;font-weight:600;color:var(--ink)">Mara Quill</div>
  <div class="abs" style="left:658px;top:2954px;font-size:14px;color:var(--muted)">Lorem Ipsum</div>

  <h2 class="abs section-title" style="top:3125px">OUR <b>GALLERY</b></h2>
  <div class="abs gallery">
    <div class="tile" role="img" aria-label="Rider on a fat-tyre e-bike by the sea" style="background:linear-gradient(160deg,#d9e2e6,#5b6a70)"></div>
    <div class="tile" role="img" aria-label="Rider mounting an e-bike, shown with a red hover overlay" style="background:#b84a55"></div>
    <div class="tile" role="img" aria-label="Woman riding an e-bike along a promenade" style="background:linear-gradient(160deg,#e6e2dc,#8a7b6c)"></div>
    <div class="tile" role="img" aria-label="Mountain biker riding through a forest trail" style="background:linear-gradient(160deg,#8a8a5a,#2c2e20)"></div>
    <div class="tile" role="img" aria-label="Two riders silhouetted against hills at sunset" style="background:linear-gradient(170deg,#d6a86a,#4a3a2a)"></div>
    <div class="tile" role="img" aria-label="Couple cycling through a flower meadow" style="background:linear-gradient(170deg,#8fb4d6,#c99a4a 70%,#6a7a3a)"></div>
    <div class="tile" role="img" aria-label="Group of friends cycling in a park" style="background:linear-gradient(170deg,#6f9a4a,#2f4a2a)"></div>
    <div class="tile" role="img" aria-label="Senior couple with electric bikes in town" style="background:linear-gradient(170deg,#9aa4b0,#4a4440)"></div>
  </div>
  <div class="abs" style="left:0;top:3756px;width:1200px;text-align:center;font-size:20px;color:var(--ink)">Follow us <span style="color:#4a6fd8">@pedal_volt</span></div>

  <section class="abs reserve">
    <h3 class="abs" style="left:112px;top:70px;width:440px">RESERVE THE PRODUCT WITH<br><span>INTIAL PAYMENT OF 10%</span></h3>
    <p class="abs" style="left:112px;top:160px;width:400px;font-size:15.5px;line-height:28px;color:var(--text)">Lorem ipsum dolor sit amet, cotetur adipiscing elit, sed do eiusmod tempor incidunt ut labore.</p>
    <div class="abs" role="img" aria-label="Black electric mountain bike, side view" style="left:720px;top:-15px;width:370px;height:335px;border-radius:30px;background:linear-gradient(135deg,#8a8a8a,#1d1d1d);opacity:.85"></div>
    <span class="abs btn btn-red" style="left:558px;top:132px;padding:0 28px">Pre-Order</span>
  </section>

  <footer class="abs footer">
    <div class="abs logo" style="left:112px;top:90px">Bicycle Sales</div>
    <div class="abs" style="left:112px;top:142px;display:flex;gap:8px"><span class="social"></span><span class="social"></span><span class="social"></span></div>

    <div class="abs" style="left:450px;top:65px">
      <div class="f-head">Quick Links</div><div class="f-bar"></div>
      <div style="margin-top:20px;font-size:13.5px;line-height:22px;position:relative;padding-left:32px">
        <svg style="position:absolute;left:2px;top:2px" width="14" height="18" viewBox="0 0 14 18"><path d="M7 0a7 7 0 017 7c0 5-7 11-7 11S0 12 0 7a7 7 0 017-7z" fill="#fff"/><circle cx="7" cy="7" r="2.5" fill="#1d1d1d"/></svg>
        Bicycle Sales,<br>Address comes here
      </div>
      <div style="margin-top:14px;font-size:13.5px;position:relative;padding-left:32px">
        <svg style="position:absolute;left:0;top:2px" width="16" height="16" viewBox="0 0 16 16"><path d="M3 1l3 1 1 4-2 1c1 2 3 4 5 5l1-2 4 1 1 3-2 2C8 16 0 8 1 3z" fill="#fff"/></svg>
        +1 555-010-2040
      </div>
      <div style="margin-top:14px;font-size:13.5px;position:relative;padding-left:32px">
        <svg style="position:absolute;left:0;top:3px" width="16" height="12" viewBox="0 0 16 12"><rect width="16" height="12" rx="1.5" fill="#fff"/><path d="M1 1l7 6 7-6" fill="none" stroke="#1d1d1d" stroke-width="1.4"/></svg>
        hello@pedalvolt.example
      </div>
    </div>

    <div class="abs" style="left:738px;top:65px">
      <div class="f-head">Quick Links</div><div class="f-bar"></div>
      <ul class="f-list"><li>› Home</li><li>› About</li><li>› Product</li><li>› Revies</li></ul>
    </div>
    <div class="abs" style="left:936px;top:65px">
      <div class="f-head">Other Links</div><div class="f-bar"></div>
      <ul class="f-list"><li>› &nbsp;Terms &amp; Conditions</li><li>› &nbsp;Privacy Statement</li><li>› &nbsp;Manuals</li><li>› &nbsp;Contact</li></ul>
    </div>
    <div class="abs" style="left:0;top:292px;width:1200px;text-align:center;font-size:13px;color:#dcdcdc">2023 Bicycle Sales. All Rights Reserved.</div>
  </footer>

</div>
</body>
</html>
```